A new updated business card. A good first impression for new customers to our business.

I need something unique. I will attached a picture of our old rubbish cards, and also our current Logo ( I think this needs an update if you have any ideas, its very basic and budget)The best way you will get to see my business is checking our Facebook page, I don't really know what else to say, but anything you want to know, ask away.www.facebook.com/tkwashandseal/

Target Market(s)

Home owners

Industry/Entity Type

Business

Contact Information for Business Card

T&K's Pressure Cleaning & Concrete Sealing
Maya 0492 615 370 maya@tkwashandseal.com
Dylan 0431 528 906 dylan@tkwashandseal.com

FB: www.facebook.com/tkwashandseal/
Website: www.tkwashandseal.net (This is pretty rubbish- we don't really use it)

100% customer satisfaction guaranteed

All aspects of Hi-Pressure Cleaning
Sealing & Re-Sealing
Roof Cleaning
Colour sealing
Decorative coatings

Free no obligation quotes

Requirements
Must have
• NO OBLIGATION FREE quotes
• 100% Customer satisfaction guaranteed
• Can you please add both names, contact details and email address on one card.
• Dylan 0431 528 906
• dylan@tkwashandseal.com
• Maya 0492 615 370
• maya@tkwashandseal.com
• Please change the services:
• Hot/Cold Hi-Pressure Cleaning
• Sealing & Re-Sealing
• Roof Cleaning
• Colour Sealing
• Decorative Coatings
• Concrete Honing
• Thanks
Nice to have
• Something a bit different, something eye catching.l

```html
<!DOCTYPE html>
<html lang="en">
<head>
<meta charset="utf-8">
<title>T&amp;K's Pressure Cleaning – Business Card</title>
<link href="https://fonts.googleapis.com/css2?family=Open+Sans:wght@400;600;700&display=swap" rel="stylesheet">
<style>
  :root {
    --backdrop: #e9e6e1;
    --sky: #1aa6e6;
    --sky-deep: #0b82c6;
    --sky-soft: #5cc3f0;
    --white: #ffffff;
    --slate: #5d5f63;
    --slate-deep: #4a4c50;
    --stripe-blue: #1e9fe3;
    --stripe-red: #e3202a;
    --ink: #3a3b3e;
    --wand-tone: #d9dadc;
  }
  * { margin: 0; padding: 0; box-sizing: border-box; }
  html, body {
    width: 1200px; height: 950px; overflow: hidden;
    background: var(--backdrop);
    font-family: "Open Sans", Arial, sans-serif;
  }
  .sheet { position: relative; width: 1200px; height: 950px; }
  .card {
    position: absolute; width: 620px; height: 354px;
    border-radius: 18px; overflow: hidden;
    box-shadow: 0 10px 28px rgba(0,0,0,.22);
  }

  /* Back of card */
  .card-back {
    left: 120px; top: 70px;
    background: linear-gradient(160deg, var(--sky-soft) 0%, var(--sky) 45%, var(--sky-deep) 100%);
  }
  .card-back svg { position: absolute; inset: 0; }
  .washer-art {
    position: absolute; left: 30px; top: 120px; width: 105px; height: 120px;
    border-radius: 14px; background: rgba(255,255,255,.28);
  }
  .services {
    position: absolute; left: 185px; width: 400px; top: 96px;
    color: var(--white); text-align: center;
    font-size: 16px; line-height: 1.5; font-weight: 400;
  }
  .services .quotes { font-weight: 700; font-size: 17px; margin-top: 6px; }
  .services .promise { font-weight: 600; font-size: 15px; }

  /* Front of card */
  .card-front { left: 460px; top: 520px; background: var(--white); }
  .card-front svg { position: absolute; inset: 0; }
  .brand {
    position: absolute; left: 32px; top: 96px; width: 262px;
    display: flex; align-items: center; gap: 12px;
  }
  .brand-wand {
    flex: none; width: 80px; height: 80px; border-radius: 12px;
    background: linear-gradient(135deg, var(--wand-tone), #bfe4f7);
  }
  .brand-name {
    color: var(--ink); font-weight: 700; font-size: 17px; line-height: 1.25;
  }
  .contacts {
    position: absolute; right: 22px; top: 36px;
    text-align: right; color: var(--white);
  }
  .contact + .contact { margin-top: 12px; }
  .contact-name { font-weight: 700; font-size: 19px; }
  .contact-phone { font-weight: 600; font-size: 19px; }
  .contact-email { font-size: 13px; opacity: .95; }
  .web {
    position: absolute; left: 26px; bottom: 18px;
    color: var(--white); font-size: 14px; line-height: 1.6;
  }
  .web-line { display: flex; align-items: center; gap: 8px; }
  .web-mark {
    width: 16px; height: 16px; border-radius: 3px; background: var(--stripe-blue);
  }
</style>
</head>
<body>
<main class="sheet">

  <section class="card card-back" aria-label="Business card back">
    <svg width="620" height="354" viewBox="0 0 620 354" aria-hidden="true">
      <ellipse cx="385" cy="180" rx="228" ry="125" fill="none" stroke="#ffffff" stroke-width="5"/>
    </svg>
    <div class="washer-art" role="img" aria-label="Pressure washer gun and lance illustration"></div>
    <div class="services">
      <p>Hot/Cold Hi-Pressure Cleaning</p>
      <p>Sealing &amp; Re-Sealing • Roof Cleaning</p>
      <p>Colour Sealing • Decorative Coatings</p>
      <p>Concrete Honing</p>
      <p class="quotes">Free no obligation quotes</p>
      <p class="promise">100% customer satisfaction guaranteed</p>
    </div>
  </section>

  <section class="card card-front" aria-label="Business card front">
    <svg width="620" height="354" viewBox="0 0 620 354" aria-hidden="true">
      <path d="M312,0 C452,34 482,226 0,290 L0,354 L620,354 L620,0 Z" fill="var(--slate)"/>
      <path d="M0,354 L0,305 C300,280 500,255 620,205 L620,354 Z" fill="var(--slate-deep)" opacity=".35"/>
      <path d="M300,0 C440,34 470,220 0,276" fill="none" stroke="var(--stripe-blue)" stroke-width="7"/>
      <path d="M312,0 C452,34 482,226 0,290" fill="none" stroke="var(--stripe-red)" stroke-width="9"/>
    </svg>

    <div class="brand">
      <div class="brand-wand" role="img" aria-label="Pressure washer lance illustration"></div>
      <p class="brand-name">T&amp;K's Pressure Cleaning &amp; Concrete Sealing</p>
    </div>

    <div class="contacts">
      <div class="contact">
        <p class="contact-name">Maya</p>
        <p class="contact-phone">0492 615 370</p>
        <p class="contact-email">maya@tkwashandseal.com</p>
      </div>
      <div class="contact">
        <p class="contact-name">Dylan</p>
        <p class="contact-phone">0431 528 906</p>
        <p class="contact-email">dylan@tkwashandseal.com</p>
      </div>
    </div>

    <div class="web">
      <p class="web-line"><span class="web-mark"></span>www.facebook.com/tkwashandseal/</p>
      <p class="web-line">www.tkwashandseal.net</p>
    </div>
  </section>

</main>
</body>
</html>
```